Re-style home page - eye-catching and unique design for social commerce website

We need a new concept design for BrinoKet's home page.
We don't want to make huge changes but creating a more professional and eye-catching style.

We need to look very serious like a professional services company and in the same time to look like a social network for e-commerce.

Our logo is very captive and you can use to creating something of harmonious.

This is a re-style and I'm excepted to see unique and fresh design like Glimmora.

Target Market(s)

e-commerce and social

Industry/Entity Type

Social

Number of Pages Required

1 page

Font styles to use
Serif
Sans Serif

Requirements
Must have
• An eye-catching result.
• Search bar with logo and Login How it works and business
• The slogan with login and signup.
• Footer links.
Nice to have
• I would like to open the home page and see only two clear ways:
• -Consumer
• --Search
• --The slogan
• --Login and Signup
• --How it works
• -Business
• --Go to Business area
• Background: City, Shopping.
Should not have
• Scrollbar style!

```html
<!DOCTYPE html>
<html lang="en">
<head>
<meta charset="utf-8">
<title>BrinoKet — Shop directly from your profile</title>
<link href="https://fonts.googleapis.com/css2?family=Montserrat:wght@400;500;600;700&display=swap" rel="stylesheet">
<style>
  :root {
    --ink: #ffffff;
    --ink-soft: #b9b9b9;
    --ink-mute: #c9c9c9;
    --accent: #e8264f;
    --social: #4a64a5;
    --panel: rgba(8, 8, 8, 0.82);
    --field: #ffffff;
    --field-text: #8a8a8a;
    --rule: rgba(255, 255, 255, 0.22);
  }
  * { box-sizing: border-box; margin: 0; padding: 0; }
  html, body {
    width: 1200px; height: 675px; overflow: hidden;
    font-family: "Montserrat", sans-serif; color: var(--ink);
    background: #1a1614;
  }
  .page { position: relative; width: 1200px; height: 675px; overflow: hidden; }

  .hero-backdrop {
    position: absolute; inset: 0;
    background:
      radial-gradient(ellipse at 30% 35%, rgba(120, 80, 50, 0.55), transparent 55%),
      radial-gradient(ellipse at 85% 30%, rgba(110, 95, 80, 0.45), transparent 50%),
      radial-gradient(ellipse at 55% 80%, rgba(70, 45, 30, 0.5), transparent 60%),
      linear-gradient(180deg, #2c2622 0%, #231d19 55%, #16120f 100%);
  }
  .hero-shade { position: absolute; inset: 0; background: rgba(0, 0, 0, 0.35); }

  .brand {
    position: absolute; left: 88px; top: 23px;
    font-size: 20px; font-weight: 600; letter-spacing: -0.3px;
    display: flex; align-items: center; gap: 7px;
  }
  .brand-mark { width: 12px; height: 12px; background: var(--accent); }

  .top-nav { position: absolute; right: 86px; top: 25px; display: flex; align-items: center; gap: 34px; }
  .top-nav .nav-link { font-size: 13px; font-weight: 500; color: var(--ink); text-decoration: none; }
  .btn-login {
    width: 73px; height: 26px; border-radius: 3px; background: var(--accent);
    display: flex; align-items: center; justify-content: center;
    font-size: 13px; font-weight: 500; color: var(--ink); text-decoration: none;
  }

  .entry-panel {
    position: absolute; left: 350px; top: 124px; width: 500px; height: 314px;
    background: var(--panel); border-radius: 10px; text-align: center;
  }
  .entry-title { margin-top: 55px; font-size: 23px; font-weight: 700; letter-spacing: -0.2px; }
  .entry-slogan { margin-top: 5px; font-size: 14px; font-weight: 500; }

  .auth-row { position: absolute; left: 61px; top: 167px; width: 378px; display: flex; align-items: center; justify-content: space-between; }
  .btn-social {
    width: 163px; height: 36px; border-radius: 3px; background: var(--social);
    display: flex; align-items: center; gap: 10px; padding-left: 10px;
    font-size: 10px; font-weight: 700; color: var(--ink);
  }
  .social-mark { width: 10px; height: 10px; background: var(--ink); border-radius: 50%; }
  .auth-or { font-size: 13px; font-weight: 500; }
  .btn-signup {
    width: 163px; height: 36px; border-radius: 3px; background: var(--accent);
    display: flex; align-items: center; justify-content: center;
    font-size: 13px; font-weight: 500; color: var(--ink);
  }
  .feed-search {
    position: absolute; left: 61px; top: 226px; width: 378px; height: 41px;
    background: var(--field); border-radius: 3px;
    display: flex; align-items: center; padding-left: 15px;
    font-size: 12.5px; color: var(--field-text);
  }

  .audience { position: absolute; left: 449px; top: 459px; display: flex; }
  .audience-item { display: flex; flex-direction: column; }
  .audience-item .label { font-size: 16px; font-weight: 600; }
  .audience-item .hint { margin-top: 5px; font-size: 10.5px; color: var(--ink-soft); }
  .audience-item.consumer { width: 138px; }
  .audience-rule { width: 1px; height: 30px; background: var(--rule); margin-top: 6px; margin-right: 27px; }

  .site-footer { position: absolute; left: 0; right: 0; top: 601px; text-align: center; }
  .footer-links { display: flex; justify-content: center; gap: 26px; padding-left: 2px; }
  .footer-links a { font-size: 10px; font-weight: 500; color: var(--ink-mute); text-decoration: none; }
  .footer-links a.current { color: var(--ink); }
  .copyright { margin-top: 17px; font-size: 9.5px; color: var(--ink-mute); }
</style>
</head>
<body>
<div class="page">
  <div class="hero-backdrop" role="img" aria-label="Blurred busy city shopping street with pedestrians and storefronts"></div>
  <div class="hero-shade"></div>

  <div class="brand"><span>BrinoKet</span><span class="brand-mark"></span></div>

  <nav class="top-nav">
    <a class="nav-link" href="#">How It Works</a>
    <a class="btn-login" href="#">Login</a>
  </nav>

  <section class="entry-panel">
    <h1 class="entry-title">Shop directly from your profile</h1>
    <p class="entry-slogan">Save your time. Live better.</p>
    <div class="auth-row">
      <div class="btn-social"><span class="social-mark"></span>Sign in with Friendlo</div>
      <span class="auth-or">or</span>
      <div class="btn-signup">Sign Up</div>
    </div>
    <div class="feed-search">Search or Setup your feed</div>
  </section>

  <div class="audience">
    <div class="audience-item consumer">
      <span class="label">Consumer</span>
      <span class="hint">Go to Consumer area</span>
    </div>
    <div class="audience-rule"></div>
    <div class="audience-item business">
      <span class="label">Business</span>
      <span class="hint">Go to Business area</span>
    </div>
  </div>

  <footer class="site-footer">
    <nav class="footer-links">
      <a class="current" href="#">About Us</a>
      <a href="#">Blog</a>
      <a href="#">Business</a>
      <a href="#">Jobs</a>
      <a href="#">Privacy</a>
      <a href="#">FAQ</a>
      <a href="#">Contacts</a>
    </nav>
    <p class="copyright">© 2015 BrinoKet. All right reserved.</p>
  </footer>
</div>
</body>
</html>
```